Web Design for company in the healthcare industry

We need a web design for a new company in the healthcare industry (telehealth) which allows patients to schedule appointments at their convenience, view and monitor their results, and consult with specialists that fit their requirements. The aim is to help patients take charge of their own health.

We already have a logo (attached) and are working with a developer who will do all the back end programming once the design is ready. Apart from the colours in the logo, we think shades of gray would work well.

Target Market(s)

I imagine the vast majority would be professionals from 30-50 years old.

Industry/Entity Type

Health And Wellness

Number of Pages Required

4 page

Requirements
Must have
• Hand-sketched graphics, particularly on landing page.
Should not have
• We don't want any photographs of people

```html
<!DOCTYPE html>
<html lang="en">
<head>
<meta charset="utf-8">
<title>Medora – Healthcare on your schedule</title>
<link href="https://fonts.googleapis.com/css2?family=Open+Sans:ital,wght@0,400;0,600;0,700;1,400;1,600&display=swap" rel="stylesheet">
<style>
:root{
  --green:#8cc63f;
  --green-dark:#74ad2b;
  --blue:#2f86c8;
  --blue-deep:#1e5f9c;
  --blue-light:#9fd0ef;
  --ink:#333a40;
  --grey:#7b8288;
  --grey-light:#e2e5e8;
  --sketch:#c9ced3;
  --paper:#ffffff;
  --footer:#5b6168;
}
*{box-sizing:border-box;margin:0;padding:0}
html,body{width:796px;height:1200px;overflow:hidden}
body{font-family:"Open Sans",Arial,sans-serif;color:var(--ink);background:var(--paper);position:relative}
.header{height:88px;display:flex;align-items:center;padding:0 60px;justify-content:space-between}
.brand{display:flex;align-items:center;gap:8px;font-size:34px;font-weight:600;color:var(--blue)}
.brand-dot{width:14px;height:14px;border-radius:50%;background:var(--green)}
.header-tools{display:flex;align-items:center;gap:24px}
.search{width:128px;height:22px;border:1px solid #cfd3d6;font-size:9px;color:#999;padding:0 8px;display:flex;align-items:center;justify-content:space-between}
.call{font-size:11px;font-weight:700;color:var(--ink)}
.call span{color:var(--blue);margin-left:4px}
.nav{height:24px;background:var(--green);display:flex;justify-content:center}
.nav a{color:#fff;text-decoration:none;font-size:9px;font-weight:600;width:120px;text-align:center;line-height:24px;border-right:1px solid rgba(255,255,255,.35)}
.nav a:last-child{border-right:0}
.hero{position:relative;height:373px;background:linear-gradient(100deg,var(--blue-deep) 0%,var(--blue) 45%,var(--blue-light) 100%);overflow:hidden}
.hero-art{position:absolute;right:0;top:0;width:300px;height:100%;background:linear-gradient(90deg,rgba(255,255,255,0),rgba(235,244,250,.8) 45%,rgba(248,251,253,.95))}
.hero-copy{position:absolute;left:64px;top:115px;width:390px;color:#fff}
.hero-copy h1{font-size:46px;font-weight:600;line-height:1}
.hero-copy p{font-size:11.5px;font-weight:600;font-style:italic;line-height:1.5;margin-top:12px}
.hero-actions{display:flex;gap:14px;margin-top:22px}
.btn{font-size:8.5px;font-weight:700;color:#fff;padding:0 18px;height:28px;line-height:28px;text-transform:uppercase}
.btn-primary{background:var(--green)}
.btn-ghost{border:1px solid #fff;line-height:26px}
.welcome{text-align:center;padding-top:40px}
.section-title{font-size:20px;font-weight:400;color:var(--ink)}
.welcome-text{width:480px;margin:12px auto 0;font-size:8px;line-height:1.7;color:var(--grey)}
.steps{display:flex;justify-content:center;align-items:flex-start;margin-top:28px}
.step{width:116px;display:flex;flex-direction:column;align-items:center}
.step-art{width:116px;height:116px;border-radius:50%;border:2px solid var(--grey-light);background:radial-gradient(circle at 50% 45%,#d6dadf 0,#e9ecee 38%,#f7f8f9 70%)}
.step-label{font-size:8.5px;font-weight:700;line-height:1.3;margin-top:10px;text-transform:uppercase}
.step-arrow{width:82px;height:116px;display:flex;align-items:center;justify-content:center}
.columns{display:flex;gap:44px;padding:40px 60px 0}
.about{width:350px}
.news{flex:1}
.col-title{font-size:18px;font-weight:400;border-bottom:1px solid var(--grey-light);padding-bottom:6px;display:flex;justify-content:space-between;align-items:flex-end}
.view-all{font-size:8px;color:var(--green);font-weight:600}
.about-body{display:flex;gap:12px;margin-top:14px}
.about-art{width:130px;height:72px;flex:none;background:linear-gradient(135deg,#cfdde8,#8fb0c9)}
.text{font-size:8px;line-height:1.6;color:var(--grey)}
.about .text + .text{margin-top:8px}
.news-item{display:flex;gap:12px;margin-top:14px}
.news-art{width:68px;height:60px;flex:none;background:linear-gradient(135deg,#dfe9f0,#9db9cf)}
.news-title{font-size:8px;font-weight:700;color:var(--green-dark)}
.news-meta{font-size:7px;color:var(--blue);margin:4px 0}
.read-more{font-size:7.5px;color:var(--green-dark);font-weight:600;margin-top:3px}
.newsletter{position:absolute;left:0;top:1068px;width:796px;height:58px;background:var(--green);display:flex;align-items:center;padding:0 60px;gap:14px;color:#fff}
.newsletter h2{font-size:15px;font-weight:400;line-height:1.15;width:180px}
.newsletter-form{display:flex;margin-left:auto}
.field{width:290px;height:26px;background:#fff;font-size:8px;color:#aaa;padding:0 10px;line-height:26px}
.subscribe{height:26px;padding:0 18px;background:var(--footer);font-size:8.5px;font-weight:700;line-height:26px}
.footer{position:absolute;left:0;top:1126px;width:796px;height:74px;background:var(--footer);color:#fff;display:flex;justify-content:space-between;align-items:center;padding:0 60px}
.footer-links{font-size:8px}
.footer-links span{margin:0 4px;opacity:.6}
.copyright{font-size:7.5px;margin-top:8px;opacity:.85}
.social{display:flex;gap:8px}
.social i{width:26px;height:26px;border:1.5px solid #fff;border-radius:50%;display:block}
</style>
</head>
<body>
<header class="header">
  <div class="brand"><span>Medora</span><i class="brand-dot"></i></div>
  <div class="header-tools">
    <div class="search">SEARCH
      <svg width="9" height="9" viewBox="0 0 10 10"><circle cx="4" cy="4" r="3" fill="none" stroke="#888" stroke-width="1.3"/><line x1="6.2" y1="6.2" x2="9" y2="9" stroke="#888" stroke-width="1.3"/></svg>
    </div>
    <div class="call">CALL US NOW |<span>1 800 555 0142</span></div>
  </div>
</header>
<nav class="nav">
  <a href="#">HOME</a><a href="#">ABOUT US</a><a href="#">HEALTH PACKAGES</a><a href="#">APPOINTMENTS</a><a href="#">SPECIALISTS</a><a href="#">CONTACT US</a>
</nav>
<section class="hero">
  <div class="hero-art" role="img" aria-label="Doctor in a white coat holding a stethoscope, over a faint heartbeat line"></div>
  <div class="hero-copy">
    <h1>Medora</h1>
    <p>We are a new company in the healthcare industry which allows patients to schedule appointments at their convenience, view and monitor their results, and consult with specialists that fit their requirements.</p>
    <div class="hero-actions">
      <span class="btn btn-primary">Book an appointment</span>
      <span class="btn btn-ghost">Get more information</span>
    </div>
  </div>
</section>
<section class="welcome">
  <h2 class="section-title">Welcome to Medora</h2>
  <p class="welcome-text">Our clinic brings care to your schedule. Book visits online, track your test results in one secure place and speak with the right specialist whenever it suits you. We keep every step simple, clear and close to home, so you stay in charge of your health.</p>
  <div class="steps">
    <div class="step"><div class="step-art" role="img" aria-label="Hand-sketched person choosing a health package"></div><div class="step-label">Select<br>a package</div></div>
    <div class="step-arrow"><svg width="40" height="12" viewBox="0 0 40 12"><line x1="0" y1="6" x2="36" y2="6" stroke="#b9bec2" stroke-width="1.5" stroke-dasharray="3 3"/><polyline points="31,1 37,6 31,11" fill="none" stroke="#b9bec2" stroke-width="1.5"/></svg></div>
    <div class="step"><div class="step-art" role="img" aria-label="Hand-sketched calendar for scheduling"></div><div class="step-label">Schedule<br>an appointment</div></div>
    <div class="step-arrow"><svg width="40" height="12" viewBox="0 0 40 12"><line x1="0" y1="6" x2="36" y2="6" stroke="#b9bec2" stroke-width="1.5" stroke-dasharray="3 3"/><polyline points="31,1 37,6 31,11" fill="none" stroke="#b9bec2" stroke-width="1.5"/></svg></div>
    <div class="step"><div class="step-art" role="img" aria-label="Hand-sketched person reviewing test results"></div><div class="step-label">Get your<br>results back</div></div>
    <div class="step-arrow"><svg width="40" height="12" viewBox="0 0 40 12"><line x1="0" y1="6" x2="36" y2="6" stroke="#b9bec2" stroke-width="1.5" stroke-dasharray="3 3"/><polyline points="31,1 37,6 31,11" fill="none" stroke="#b9bec2" stroke-width="1.5"/></svg></div>
    <div class="step"><div class="step-art" role="img" aria-label="Hand-sketched cheerful healthy person"></div><div class="step-label">A<br>healthier you</div></div>
  </div>
</section>
<section class="columns">
  <div class="about">
    <h3 class="col-title">A few Word About us</h3>
    <div class="about-body">
      <div class="about-art" role="img" aria-label="Medical report with stethoscope and pills on a desk"></div>
      <p class="text">Medora started with one simple idea: good care should fit around your life. Our team of doctors and nurses works online and in person to guide you from first booking to final result.</p>
    </div>
    <p class="text">We listen first. Every plan is shaped by your needs, your history and your goals, and every specialist is chosen to match them closely.</p>
  </div>
  <div class="news">
    <h3 class="col-title">Our News <span class="view-all">VIEW ALL</span></h3>
    <article class="news-item">
      <div class="news-art" role="img" aria-label="Tablet showing health charts"></div>
      <div>
        <div class="news-title">SED UT PERSPICIATIS UNDE OMNIS ISTE</div>
        <div class="news-meta">20/03/2015 &nbsp; Admin &nbsp; 3 Comments</div>
        <p class="text">Short health tips and clinic updates from our team, written to help you stay well.</p>
        <div class="read-more">Read More »</div>
      </div>
    </article>
    <article class="news-item">
      <div class="news-art" role="img" aria-label="Doctor's desk with medical tools"></div>
      <div>
        <div class="news-title">SED UT PERSPICIATIS UNDE OMNIS ISTE</div>
        <div class="news-meta">20/03/2015 &nbsp; Admin &nbsp; 3 Comments</div>
        <p class="text">Short health tips and clinic updates from our team, written to help you stay well.</p>
        <div class="read-more">Read More »</div>
      </div>
    </article>
  </div>
</section>
<section class="newsletter">
  <svg width="34" height="26" viewBox="0 0 34 26"><rect x="1" y="1" width="32" height="24" fill="none" stroke="#fff" stroke-width="1.8"/><polyline points="1,1 17,14 33,1" fill="none" stroke="#fff" stroke-width="1.8"/></svg>
  <h2>Newsletter<br>Subscription</h2>
  <div class="newsletter-form"><div class="field">Email Address</div><div class="subscribe">SUBSCRIBE</div></div>
</section>
<footer class="footer">
  <div>
    <div class="footer-links">Home<span>|</span>About Us<span>|</span>Health Packages<span>|</span>Appointments<span>|</span>Specialists<span>|</span>Contact Us</div>
    <div class="copyright">Copyright © Medora 2015. All rights Reserved</div>
  </div>
  <div class="social"><i></i><i></i><i></i><i></i></div>
</footer>
</body>
</html>
```